Mindfulness School for Children -- Business Cards

We're looking for business cards for our school directors and owners. We're a mindfulness school for children called little lanterns. Attached are our logos/icons.

```html
<!DOCTYPE html>
<html lang="en">
<head>
<meta charset="utf-8">
<title>little lanterns — business cards</title>
<link rel="stylesheet" href="https://fonts.googleapis.com/css2?family=Alegreya:wght@400&family=Arimo:wght@400&display=swap">
<style>
  :root {
    --backdrop: #1b1b1b;
    --card: #0c0c0c;
    --card-edge: #1f1f1f;
    --teal: #5cb8c9;
    --sea-green: #6fbf9e;
    --ink-light: #f2f2f2;
    --silver: #c9c9c9;
    --divider: #4f9f8a;
  }
  * { box-sizing: border-box; margin: 0; padding: 0; }
  html, body {
    width: 1200px; height: 900px; overflow: hidden;
    background: var(--backdrop);
  }
  .sheet {
    width: 1200px; height: 900px;
    display: flex; align-items: center; justify-content: center; gap: 40px;
  }
  .card {
    position: relative;
    width: 540px; height: 310px;
    background: var(--card);
    border-radius: 22px;
    border: 1px solid var(--card-edge);
    box-shadow: 0 18px 40px rgba(0,0,0,.6);
    overflow: hidden;
  }
  .wordmark {
    font-family: "Alegreya", Georgia, serif;
    font-weight: 400;
    letter-spacing: .5px;
    white-space: nowrap;
  }
  .card--front .wordmark {
    position: absolute; left: 0; right: 0; top: 62px;
    text-align: center; font-size: 50px; color: var(--teal);
  }
  .identity {
    position: absolute; top: 168px; left: 70px;
    width: 190px; text-align: right;
  }
  .identity__name {
    font-family: "Alegreya", Georgia, serif;
    font-size: 27px; color: var(--sea-green); line-height: 1.05;
  }
  .identity__role {
    font-family: "Arimo", Arial, sans-serif;
    font-size: 15px; color: var(--ink-light); margin-top: 2px;
  }
  .divider {
    position: absolute; left: 278px; top: 150px;
    width: 1px; height: 78px; background: var(--divider);
  }
  .contacts {
    position: absolute; left: 294px; top: 150px;
    list-style: none;
    font-family: "Arimo", Arial, sans-serif;
    font-size: 14px; color: var(--ink-light);
  }
  .contacts li { display: flex; align-items: center; gap: 7px; height: 26px; }
  .contacts svg { width: 15px; height: 15px; flex: none; }
  .contacts .accent { color: var(--sea-green); }
  .address {
    position: absolute; left: 0; right: 0; bottom: 34px;
    display: flex; justify-content: center; align-items: center; gap: 8px;
    font-family: "Arimo", Arial, sans-serif; font-size: 15px; color: var(--ink-light);
  }
  .address svg { width: 14px; height: 18px; }
  .card--back { display: flex; align-items: center; justify-content: center; }
  .card--back .wordmark { font-size: 50px; color: var(--silver); }
</style>
</head>
<body>
<main class="sheet">
  <section class="card card--front" aria-label="Business card front">
    <div class="wordmark">little lanterns</div>

    <div class="identity">
      <p class="identity__name">Daniel Hart</p>
      <p class="identity__role">Managing Director</p>
    </div>

    <div class="divider"></div>

    <ul class="contacts">
      <li>
        <svg viewBox="0 0 16 16" fill="none" stroke="var(--teal)" stroke-width="1.6" stroke-linecap="round" stroke-linejoin="round"><path d="M3 2.5l2.5-.5 1.5 3.2-1.6 1.2a8 8 0 0 0 4.2 4.2l1.2-1.6 3.2 1.5-.5 2.5c-6 .5-11-4.5-10.5-10.5z"/></svg>
        044-555 218 604
      </li>
      <li>
        <svg viewBox="0 0 16 16" fill="none" stroke="var(--teal)" stroke-width="1.6" stroke-linejoin="round"><rect x="1.5" y="3.5" width="13" height="9" rx="1"/><path d="M1.5 4l6.5 5 6.5-5"/></svg>
        hello@lanternmail.com
      </li>
      <li>
        <svg viewBox="0 0 16 16" fill="none" stroke="var(--teal)" stroke-width="1.4"><circle cx="8" cy="8" r="6.3"/><ellipse cx="8" cy="8" rx="2.8" ry="6.3"/><path d="M1.7 8h12.6M3 4.7h10M3 11.3h10"/></svg>
        www.<span class="accent">lanternschool</span>.com
      </li>
    </ul>

    <p class="address">
      <svg viewBox="0 0 14 18"><path d="M7 1a6 6 0 0 1 6 6c0 4.5-6 10-6 10S1 11.5 1 7a6 6 0 0 1 6-6z" fill="var(--teal)"/><circle cx="7" cy="7" r="2.2" fill="var(--card)"/></svg>
      17, Willow Park Lane 20914, Northvale
    </p>
  </section>

  <section class="card card--back" aria-label="Business card back">
    <div class="wordmark">little lanterns</div>
  </section>
</main>
</body>
</html>
```